Modern Label for cleaning products for the brand Vorlix

We need a label design for our line of cleaning products. The label should feature our logo and an image to identify the product's intended use. I've added our logo and an image for use. This only concerns the design of the label on the front of the bottle.

Label dimensions:
Label 1 (500ml bottle with spray): width 58mm x height 115mm
Label 2: (1L bottle): width 73mm x height 140mm
The design must be consistent for both bottles which you find in the pictures.

The bottles to be labeled are white. See the attachment for a photo of the bottles.

The photo must also appear on the label to identify the product's intended use.

Product information:
Brand: Vorlix
Product: Sanitary Cleaner

This text must be placed on the label:
"Cleans, descales & freshens. followed with this text: "Ideal for quick and powerful cleaning. A ready-to-use product for everyday use."

- Mention the seperate USP's: Sanitary, Bathroom, Toilet, Wet areas

Appearance: This is a consumer product, but it must have a professional appearance. We would like to see a design that use the color blue from our logo.

Target Market(s)

Consumers who take care of their homes and want to maintain it the correct (professional) way

Font styles to use
Sans Serif

Colors
0054AA
0677BA
7BADD7
CADEEF
E8F1F8

Requirements
Must have
• USP's + use of image and logo + blend in 1 design
Nice to have
• Keep the color of the logo in the design
Should not have
• Comic sans

```html
<!DOCTYPE html>
<html lang="en">
<head>
<meta charset="utf-8">
<title>Vorlix Sanitary Cleaner – Front Labels</title>
<link rel="stylesheet" href="https://fonts.googleapis.com/css2?family=Montserrat:wght@400;700;800&family=Raleway:wght@500&family=Open+Sans:wght@400&display=swap">
<style>
  :root {
    --blue-deep: #0054AA;
    --blue-mid: #0677BA;
    --blue-soft: #7BADD7;
    --blue-pale: #CADEEF;
    --blue-mist: #E8F1F8;
    --navy: #15386e;
    --ink: #1d1d1f;
    --white: #ffffff;
  }
  * { box-sizing: border-box; margin: 0; padding: 0; }
  html, body { width: 1200px; height: 810px; overflow: hidden; }
  body {
    background: var(--blue-mist);
    display: flex;
    align-items: center;
    justify-content: center;
    gap: 120px;
  }
  .label {
    position: relative;
    width: 30.7em;
    height: 59em;
    display: flex;
    flex-direction: column;
    align-items: center;
    overflow: hidden;
    border-radius: 45% 45% 0.6em 0.6em / 7% 7% 0.6em 0.6em;
    background: linear-gradient(to bottom,
      var(--white) 0%, var(--white) 55%,
      #e3eef8 66%, var(--blue-soft) 85%, var(--blue-deep) 100%);
    box-shadow: 0 10px 30px rgba(0, 84, 170, 0.18);
    font-family: "Montserrat", sans-serif;
  }
  .label > * { flex-shrink: 0; }
  .label--500ml { font-size: 10px; }
  .label--1l { font-size: 12.57px; }

  .brand { display: flex; flex-direction: column; align-items: center; margin-top: 3.3em; }
  .brand__mark {
    width: 6.8em; height: 6.8em; border-radius: 50%;
    border: 1em solid var(--blue-mid);
  }
  .brand__name {
    margin-top: 0.15em;
    font-weight: 800; font-size: 3.2em; line-height: 1.1;
    color: var(--ink); letter-spacing: -0.01em;
  }
  .product-title {
    font-size: 1em; text-align: center; margin-top: 0.3em;
    line-height: 1; white-space: nowrap;
  }
  .product-title__main {
    display: block; font-weight: 800; font-size: 3.8em;
    color: var(--blue-deep); letter-spacing: 0.01em;
  }
  .product-title__sub {
    display: block; font-weight: 400; font-size: 3.3em;
    color: var(--blue-mid); letter-spacing: 0.02em; margin-top: 0.05em;
  }
  .usage-photo {
    width: 100%; height: 15.3em; margin-top: 0.3em;
    background: linear-gradient(110deg, #8d8579 0%, #c9b9a0 35%, #efe3cc 50%, #b7ab99 70%, #6f6556 100%);
  }
  .usp-list {
    list-style: none; display: flex; justify-content: center;
    gap: 1.4em; margin-top: 0.2em;
  }
  .usp { display: flex; flex-direction: column; align-items: center; width: 5.2em; }
  .usp__icon {
    width: 4.6em; height: 4.6em; border-radius: 50%;
    background: radial-gradient(circle at 40% 35%, #2e9be0, var(--blue-mid) 60%);
    border: 0.2em solid var(--navy);
    display: flex; align-items: center; justify-content: center;
  }
  .usp__icon svg { width: 2.7em; height: 2.7em; }
  .usp__text {
    font-family: "Open Sans", sans-serif; font-size: 1.1em;
    color: var(--ink); margin-top: 0.6em; white-space: nowrap;
  }
  .claim {
    font-family: "Raleway", sans-serif; font-weight: 500;
    font-size: 2.7em; line-height: 1.15; text-align: center;
    color: var(--ink); margin-top: 0.25em; white-space: nowrap;
  }
  .description {
    font-family: "Open Sans", sans-serif; font-size: 1.15em;
    line-height: 1.5; text-align: center; color: var(--navy);
    margin-top: 0.4em; white-space: nowrap;
  }
  .spacer { flex: 1 1 auto; }
  .badge {
    font-family: "Open Sans", sans-serif; font-size: 1.6em;
    color: var(--white); background: var(--navy);
    padding: 0.05em 0.6em; border-radius: 0.15em;
    margin-bottom: 1.6em;
  }
</style>
</head>
<body>

<svg width="0" height="0" style="position:absolute" aria-hidden="true">
  <defs>
    <symbol id="icon-shower" viewBox="0 0 28 28">
      <path d="M19 26V7a3 3 0 0 0-6 0v1" fill="none" stroke="#fff" stroke-width="2"/>
      <path d="M7 13a6 6 0 0 1 12 0z" fill="#fff"/>
      <g fill="#fff"><circle cx="9" cy="16" r="1"/><circle cx="13" cy="16" r="1"/><circle cx="17" cy="16" r="1"/><circle cx="8" cy="20" r="1"/><circle cx="12" cy="20" r="1"/><circle cx="16" cy="20" r="1"/></g>
    </symbol>
    <symbol id="icon-bath" viewBox="0 0 28 28">
      <path d="M3 14h22v3a6 6 0 0 1-6 6H9a6 6 0 0 1-6-6z" fill="#fff"/>
      <path d="M20 14V6a2 2 0 0 1 4 0" fill="none" stroke="#fff" stroke-width="1.6"/>
      <path d="M7 23l-1 3M21 23l1 3" stroke="#fff" stroke-width="1.6"/>
    </symbol>
    <symbol id="icon-toilet" viewBox="0 0 28 28">
      <rect x="7" y="2" width="14" height="8" rx="1.5" fill="#fff"/>
      <path d="M5 12h18a9 7 0 0 1-5 8v5H10v-5a9 7 0 0 1-5-8z" fill="#fff"/>
    </symbol>
    <symbol id="icon-drop" viewBox="0 0 28 28">
      <path d="M14 3c4 6 8 10 8 15a8 8 0 0 1-16 0c0-5 4-9 8-15z" fill="#fff"/>
      <path d="M11 16a4 4 0 0 0 2 6" fill="none" stroke="#0677BA" stroke-width="1.6"/>
    </symbol>
  </defs>
</svg>

<article class="label label--500ml">
  <header class="brand">
    <span class="brand__mark"></span>
    <span class="brand__name">vorlix</span>
  </header>
  <h1 class="product-title">
    <span class="product-title__main">SANITARY</span>
    <span class="product-title__sub">CLEANER</span>
  </h1>
  <div class="usage-photo" role="img" aria-label="Photo of a gloved hand spraying cleaner in a bright bathroom with a sink and tap"></div>
  <ul class="usp-list">
    <li class="usp"><span class="usp__icon"><svg><use href="#icon-shower"/></svg></span><span class="usp__text">Sanitary</span></li>
    <li class="usp"><span class="usp__icon"><svg><use href="#icon-bath"/></svg></span><span class="usp__text">Bathroom</span></li>
    <li class="usp"><span class="usp__icon"><svg><use href="#icon-toilet"/></svg></span><span class="usp__text">Toilet</span></li>
    <li class="usp"><span class="usp__icon"><svg><use href="#icon-drop"/></svg></span><span class="usp__text">Wet Areas</span></li>
  </ul>
  <p class="claim">Cleans, descales<br>&amp; freshens</p>
  <p class="description">Ideal for quick and powerful cleaning.<br>A ready-to-use product for everyday use.</p>
  <div class="spacer"></div>
  <span class="badge">READ-TO-USE</span>
</article>

<article class="label label--1l">
  <header class="brand">
    <span class="brand__mark"></span>
    <span class="brand__name">vorlix</span>
  </header>
  <h1 class="product-title">
    <span class="product-title__main">SANITARY</span>
    <span class="product-title__sub">CLEANER</span>
  </h1>
  <div class="usage-photo" role="img" aria-label="Photo of a gloved hand spraying cleaner in a bright bathroom with a sink and tap"></div>
  <ul class="usp-list">
    <li class="usp"><span class="usp__icon"><svg><use href="#icon-shower"/></svg></span><span class="usp__text">Sanitary</span></li>
    <li class="usp"><span class="usp__icon"><svg><use href="#icon-bath"/></svg></span><span class="usp__text">Bathroom</span></li>
    <li class="usp"><span class="usp__icon"><svg><use href="#icon-toilet"/></svg></span><span class="usp__text">Toilet</span></li>
    <li class="usp"><span class="usp__icon"><svg><use href="#icon-drop"/></svg></span><span class="usp__text">Wet Areas</span></li>
  </ul>
  <p class="claim">Cleans, descales<br>&amp; freshens</p>
  <p class="description">Ideal for quick and powerful cleaning.<br>A ready-to-use product for everyday use.</p>
  <div class="spacer"></div>
  <span class="badge">READ-TO-USE</span>
</article>

</body>
</html>
```